New Business Card Design Project

I need a design for business cards, i am an electrical business called "Corvane Electrical and Communications" i need the cards to be double sided with the company logo on the back (attached) the front needs to say my company name, web site, email address, telephone number, and ABN number and electrical license number. I am open to different arrangements of the information but would like the background to be incorporating something electrical or something that looks smart. open to all additional ideas also.

The company colours are orange and grey see logo attached.

Business Name: Corvane Electrical and Communications
Website: corvaneelectricalandcomms.example.com.au
Email: brent@corvaneelectricalandcomms.example.com.au
Telephone(mobile): 0481209736
ABN: 71208349162
Lic No: 418273D

Target Market(s)

Business entities, Project Managers, Accounts, Clients

Industry/Entity Type

Electrician

Contact Information for Business Card

I need a design for business cards, i am an electrical business called "Corvane Electrical and Communications" i need the cards to be double sided with the company logo on the back (attached) the front needs to say my company name

Font styles to use
Serif
Sans Serif

Colors
f37122
5c5c5c

Requirements
Must have
• Must have the Logo on the back open to different ways of it being on the back but had in mind to keep it central but again open to other options
Nice to have
• A real modern cool background that is eye catching yet contemporary
Should not have
• No backgrounds of a light bulb or plug or anything like that

```html
<!DOCTYPE html>
<html lang="en">
<head>
<meta charset="utf-8">
<title>Corvane Electrical and Communications – Business Cards</title>
<link rel="stylesheet" href="https://fonts.googleapis.com/css2?family=Montserrat:wght@500;600;700&display=swap">
<style>
  :root {
    --bg: #2a2a2a;
    --card: #151515;
    --orange: #f7a21b;
    --grey: #5c5c5c;
    --grey-light: #6e6e6e;
  }
  html, body {
    margin: 0;
    width: 1200px;
    height: 1189px;
    overflow: hidden;
    background: var(--bg);
    font-family: "Montserrat", sans-serif;
  }
  .card {
    position: absolute;
    left: 150px;
    width: 900px;
    height: 514px;
    background: var(--card);
    border-radius: 28px;
    box-shadow: 0 12px 30px rgba(0,0,0,.45);
    overflow: hidden;
  }
  .card--back { top: 50px; }
  .card--front { top: 614px; }

  /* Back: centred wordmark */
  .wordmark {
    position: absolute;
    left: 0; right: 0;
    top: 180px;
    text-align: center;
    color: var(--grey);
    font-weight: 600;
    line-height: 1;
  }
  .wordmark__name { font-size: 112px; letter-spacing: 6px; }
  .wordmark__tag { font-size: 24px; letter-spacing: 3px; margin-top: 14px; }

  /* Front */
  .front-mark {
    position: absolute;
    left: 56px;
    top: 70px;
    color: var(--grey);
    font-weight: 600;
    line-height: 1;
  }
  .front-mark .wordmark__name { font-size: 96px; letter-spacing: 5px; }
  .front-mark .wordmark__tag { font-size: 22px; letter-spacing: 2.5px; margin-top: 10px; }

  .social {
    position: absolute;
    top: 40px;
    right: 48px;
    display: flex;
    gap: 12px;
  }
  .social__box {
    width: 34px; height: 34px;
    border-radius: 4px;
    background: var(--orange);
  }

  .person {
    position: absolute;
    right: 48px;
    top: 210px;
    text-align: right;
  }
  .person__name { color: var(--grey-light); font-size: 32px; font-weight: 600; }
  .person__role { color: var(--orange); font-size: 20px; font-weight: 600; margin-top: 4px; }

  .divider {
    position: absolute;
    left: 56px;
    right: 48px;
    top: 300px;
    height: 2px;
    background: var(--orange);
  }

  .contact {
    position: absolute;
    left: 56px;
    bottom: 44px;
    list-style: none;
    margin: 0; padding: 0;
  }
  .contact__item {
    display: flex;
    align-items: center;
    gap: 14px;
    height: 38px;
    color: var(--grey-light);
    font-size: 21px;
    font-weight: 600;
  }
  .contact__icon {
    width: 28px; height: 28px;
    border-radius: 5px;
    background: var(--orange);
    display: flex;
    align-items: center;
    justify-content: center;
  }

  .licence {
    position: absolute;
    right: 48px;
    bottom: 118px;
    text-align: right;
    font-size: 21px;
    font-weight: 600;
    line-height: 1.5;
  }
  .licence__label { color: var(--orange); }
  .licence__value { color: var(--grey-light); }
</style>
</head>
<body>

<section class="card card--back" aria-label="Card back">
  <div class="wordmark">
    <div class="wordmark__name">CORVANE</div>
    <div class="wordmark__tag">ELECTRICAL &amp; COMMUNICATIONS</div>
  </div>
</section>

<section class="card card--front" aria-label="Card front">
  <div class="front-mark">
    <div class="wordmark__name">CORVANE</div>
    <div class="wordmark__tag">ELECTRICAL &amp; COMMUNICATIONS</div>
  </div>

  <div class="social" aria-label="Social links">
    <span class="social__box"></span>
    <span class="social__box"></span>
  </div>

  <div class="person">
    <div class="person__name">Employee Name</div>
    <div class="person__role">Principal</div>
  </div>

  <div class="divider"></div>

  <div class="licence">
    <div><span class="licence__label">Lic No:</span> <span class="licence__value">418273D</span></div>
    <div><span class="licence__label">ABN:</span> <span class="licence__value">71208349162</span></div>
  </div>

  <ul class="contact">
    <li class="contact__item">
      <span class="contact__icon">
        <svg width="16" height="18" viewBox="0 0 16 18" aria-hidden="true"><rect x="3" y="1" width="10" height="16" rx="2" fill="none" stroke="#151515" stroke-width="2"/><rect x="6" y="13" width="4" height="2" fill="#151515"/></svg>
      </span>
      0481209736
    </li>
    <li class="contact__item">
      <span class="contact__icon">
        <svg width="18" height="14" viewBox="0 0 18 14" aria-hidden="true"><rect x="1" y="1" width="16" height="12" fill="none" stroke="#151515" stroke-width="2"/><path d="M1 1 L9 8 L17 1" fill="none" stroke="#151515" stroke-width="2"/></svg>
      </span>
      brent@corvaneelectricalandcomms.example.com.au
    </li>
    <li class="contact__item">
      <span class="contact__icon">
        <svg width="18" height="18" viewBox="0 0 18 18" aria-hidden="true"><circle cx="9" cy="9" r="7.5" fill="none" stroke="#151515" stroke-width="1.8"/><ellipse cx="9" cy="9" rx="3.2" ry="7.5" fill="none" stroke="#151515" stroke-width="1.5"/><line x1="1.5" y1="9" x2="16.5" y2="9" stroke="#151515" stroke-width="1.5"/></svg>
      </span>
      corvaneelectricalandcomms.example.com.au
    </li>
  </ul>
</section>

</body>
</html>
```